Development of the overall look and feel for the website. www.ReelPalsHub.com

This site is geared as a competitor to some of the major Fan websites. Where we want to be different is making a site geared more towards interaction with the Fans in the Social Media platform.
-Live streaming
-Instant Messaging
-Ability to request and purchase custom digital pieces
-Ability for Models/creators to sell blogs, podcasts, clips, screensavers, etc. through a dedicated online digital store.
-We will also have story like features similar to those found on Photoburst to allow interaction.
-Content Creators keep 85% of earnings

This should be sexy, seductive, bold, and geared towards all spectrums. From Swingers, Kink, Fetish, Milf, College, etc.

Overall the feeling should be Fun with a sense of excitement that is taboo and erotic while not scaring people away.

Trying to find the perfect blend between finding harmony/Norma Whitcombe/GBT/SoloPatron/Velvet Soiree and KRV. Monetization will be most similar to SoloPatron.

Target Market(s)

Target market should be 18+ / All Genders/ All sexuality. I want to be sure to target markets that were traditionally left out from some of the bigger platforms with all lifestyle and gender inclusion.

Industry/Entity Type

Adult Modeling, Adult Website, Streaming, Porn/fetish

Colors

Designer to choose colors to be used in the design.

Requirements
Must have
• Sex Appeal, Curiosity, Call to action, Storyboard to tell what we are about
Nice to have
• uploaded some designs that have overall look/feel.
Should not have
• Sexy but no nudity

```html
<!DOCTYPE html>
<html lang="en">
<head>
<meta charset="utf-8">
<title>ReelPalsHub – Live Room</title>
<link href="https://fonts.googleapis.com/css2?family=Nunito:ital,wght@0,400;0,600;0,700;1,400&display=swap" rel="stylesheet">
<style>
  :root {
    --header-bg: #dcdcdc;
    --page-bg: #f5f3f3;
    --panel-bg: #ffffff;
    --bubble-bg: #f4f3f3;
    --accent: #d9535f;
    --ink: #1e1e1e;
    --muted: #555555;
    --line: #c9c9cc;
  }
  * { box-sizing: border-box; margin: 0; padding: 0; }
  html, body { width: 1200px; height: 720px; overflow: hidden; }
  body { background: var(--page-bg); font-family: "Nunito", sans-serif; color: var(--ink); position: relative; }

  .site-header { position: absolute; left: 0; top: 0; width: 1200px; height: 70px; background: var(--header-bg); }
  .brand { position: absolute; left: 22px; top: 27px; display: flex; align-items: center; gap: 6px; font-size: 11px; font-weight: 700; color: var(--ink); }
  .brand-dot { width: 14px; height: 14px; border-radius: 50%; background: var(--accent); }

  .profile { position: absolute; left: 730px; top: 12px; display: flex; align-items: center; gap: 9px; }
  .profile-avatar { width: 46px; height: 46px; border-radius: 50%; border: 1.5px solid var(--accent); padding: 3px; }
  .profile-avatar span { display: block; width: 100%; height: 100%; border-radius: 50%; background: radial-gradient(circle at 50% 40%, #c89a84, #6b4c44); }
  .profile-name { font-size: 13px; font-weight: 600; line-height: 1.25; }
  .profile-sub { font-size: 11.5px; color: var(--ink); line-height: 1.4; }
  .settings { position: absolute; left: 904px; top: 20px; }

  .btn { position: absolute; top: 16px; height: 35px; background: var(--accent); color: #fff; font-size: 13.5px; font-weight: 600; display: flex; align-items: center; justify-content: center; letter-spacing: .3px; }
  .btn-purchase { left: 958px; width: 96px; }
  .btn-request { left: 1070px; width: 97px; top: 16px; }

  .stream { position: absolute; left: 26px; top: 96px; width: 784px; height: 497px;
    background: radial-gradient(ellipse 38% 55% at 50% 62%, #6c6a55 0%, #7d7769 45%, transparent 70%), linear-gradient(180deg, #9a8f88 0%, #c8c1bb 50%, #bdb3ab 100%); }
  .live-badge { position: absolute; left: 16px; top: 18px; width: 57px; height: 26px; background: #fff; display: flex; align-items: center; justify-content: center; gap: 7px; font-size: 11.5px; font-weight: 600; }
  .live-badge::before { content: ""; width: 7px; height: 7px; border-radius: 50%; background: var(--accent); }

  .tools { position: absolute; top: 622px; left: 0; width: 820px; }
  .tool { position: absolute; width: 80px; margin-left: -40px; text-align: center; font-size: 11px; color: var(--ink); }
  .tool-icon { width: 39px; height: 39px; border-radius: 50%; background: #fff; margin: 0 auto 9px; display: flex; align-items: center; justify-content: center; box-shadow: 0 1px 3px rgba(0,0,0,.05); }

  .chat { position: absolute; left: 842px; top: 96px; width: 325px; height: 590px; background: var(--panel-bg); }
  .chat-title { position: absolute; left: 20px; top: 17px; font-size: 15.5px; font-weight: 600; line-height: 1.2; }
  .avatar { position: absolute; left: 21px; width: 42px; height: 42px; border-radius: 50%; }
  .bubble { position: absolute; background: var(--bubble-bg); font-size: 12px; color: var(--ink); }
  .bubble-short { left: 76px; height: 29px; padding: 0 11px; line-height: 29px; white-space: nowrap; }
  .bubble-long { left: 76px; width: 200px; padding: 11px 14px; line-height: 1.4; }
  .bubble-out { left: 127px; width: 178px; padding: 11px 17px; line-height: 1.2; }

  .composer { position: absolute; left: 20px; top: 526px; width: 285px; height: 45px; border: 1.5px solid var(--line); display: flex; align-items: center; padding: 0 10px 0 13px; }
  .composer-placeholder { flex: 1; font-size: 10.5px; font-style: italic; color: var(--muted); }
  .composer-actions { display: flex; gap: 10px; align-items: center; }
</style>
</head>
<body>
  <header class="site-header">
    <div class="brand"><span class="brand-dot"></span>ReelPalsHub</div>

    <div class="profile">
      <div class="profile-avatar"><span role="img" aria-label="Creator profile photo"></span></div>
      <div>
        <div class="profile-name">R. HALLOWAY</div>
        <div class="profile-sub">Tap to add Stories</div>
      </div>
    </div>

    <svg class="settings" width="28" height="28" viewBox="0 0 24 24" fill="none" stroke="#555" stroke-width="1.2" aria-label="Settings">
      <circle cx="12" cy="12" r="3.2"/>
      <path d="M12 2.5l1.6 2.3 2.7-.8.6 2.8 2.8.6-.8 2.7 2.3 1.6-2.3 1.6.8 2.7-2.8.6-.6 2.8-2.7-.8L12 21.5l-1.6-2.3-2.7.8-.6-2.8-2.8-.6.8-2.7L2.5 12l2.3-1.6-.8-2.7 2.8-.6.6-2.8 2.7.8z"/>
    </svg>

    <div class="btn btn-purchase">PURCHASE</div>
    <div class="btn btn-request">REQUEST</div>
  </header>

  <section class="stream" role="img" aria-label="Live video stream of a creator wearing headphones in a bright kitchen">
    <div class="live-badge">LIVE</div>
  </section>

  <nav class="tools">
    <div class="tool" style="left:277px">
      <div class="tool-icon"><svg width="14" height="14" viewBox="0 0 24 24" fill="none" stroke="#222" stroke-width="1.6"><rect x="2" y="6" width="14" height="12" rx="1.5"/><path d="M16 10l6-3v10l-6-3z"/></svg></div>Cam</div>
    <div class="tool" style="left:339px">
      <div class="tool-icon"><svg width="14" height="14" viewBox="0 0 24 24" fill="none" stroke="#222" stroke-width="1.6"><rect x="9" y="2" width="6" height="12" rx="3"/><path d="M5 11a7 7 0 0 0 14 0M12 18v4M8 22h8"/></svg></div>Mic</div>
    <div class="tool" style="left:396px">
      <div class="tool-icon"><svg width="14" height="14" viewBox="0 0 24 24" fill="none" stroke="#222" stroke-width="1.6"><path d="M4 20l1-5L16 4l4 4L9 19zM3 22h18"/></svg></div>Blog</div>
    <div class="tool" style="left:460px">
      <div class="tool-icon"><svg width="16" height="14" viewBox="0 0 24 24" fill="none" stroke="#222" stroke-width="1.6"><circle cx="12" cy="12" r="2.5"/><path d="M7.5 7.5a6.5 6.5 0 0 0 0 9M16.5 7.5a6.5 6.5 0 0 1 0 9M4.5 4.5a10.5 10.5 0 0 0 0 15M19.5 4.5a10.5 10.5 0 0 1 0 15"/></svg></div>Podcast</div>
    <div class="tool" style="left:527px">
      <div class="tool-icon"><svg width="15" height="14" viewBox="0 0 24 24" fill="none" stroke="#222" stroke-width="1.6"><rect x="2" y="4" width="20" height="16" rx="1"/><path d="M2 8h20M10 11l5 3-5 3z"/></svg></div>clips</div>
    <div class="tool" style="left:598px">
      <div class="tool-icon"><svg width="15" height="14" viewBox="0 0 24 24" fill="none" stroke="#222" stroke-width="1.6"><rect x="3" y="3" width="18" height="13" rx="1"/><rect x="6" y="6" width="12" height="7"/><path d="M3 20h18"/></svg></div>screensaver</div>
  </nav>

  <aside class="chat">
    <h2 class="chat-title">Chat</h2>

    <span class="avatar" role="img" aria-label="Fan avatar" style="top:50px;background:#6d5a52"></span>
    <div class="bubble bubble-short" style="top:55px">Lorem Ipsum is simply</div>

    <span class="avatar" role="img" aria-label="Fan avatar" style="top:104px;background:#7a6355"></span>
    <div class="bubble bubble-short" style="top:109px">Lorem Ipsum is simply</div>

    <div class="bubble bubble-out" style="top:162px">There are many variati ons of passages of Lorem Ipsum</div>

    <span class="avatar" role="img" aria-label="Fan avatar" style="top:251px;background:#5c9cb4"></span>
    <div class="bubble bubble-long" style="top:256px">It is a long established fact that a reader will be distracted by the readable content</div>

    <div class="bubble bubble-out" style="top:353px">There are many variati ons of passages of Lorem Ipsum</div>

    <span class="avatar" role="img" aria-label="Fan avatar" style="top:450px;background:#5e7a55"></span>
    <div class="bubble bubble-short" style="top:455px">Lorem Ipsum is simply</div>

    <div class="composer">
      <span class="composer-placeholder">Write your message</span>
      <div class="composer-actions">
        <svg width="14" height="14" viewBox="0 0 24 24" fill="none" stroke="#333" stroke-width="2"><path d="M10 14a4 4 0 0 0 5.7 0l3.5-3.5a4 4 0 0 0-5.7-5.7L12 6.3M14 10a4 4 0 0 0-5.7 0l-3.5 3.5a4 4 0 0 0 5.7 5.7L12 17.7"/></svg>
        <svg width="14" height="14" viewBox="0 0 24 24" fill="none" stroke="#333" stroke-width="2"><path d="M3 7h4l2-3h6l2 3h4v13H3z"/><circle cx="12" cy="13" r="3.5"/></svg>
        <svg width="18" height="16" viewBox="0 0 24 24" fill="var(--accent)"><path d="M2 4l20 1-9 17-2-9z"/></svg>
      </div>
    </div>
  </aside>
</body>
</html>
```